Plakat-Design für Pfandhaus gesucht
Zielgruppe
Wir sind ein Pfandhaus wir vergeben Pfandkredite gegen Wertgegenstände sowie Juwelier und Goldankauf aber in erster Linie steht das Pfandhaus .
Aufgabenstellung
Ich möchte gerne Plakate Buchen die an Straßen oder Hauswänden befestigt sind. Ca.3,5x3 Meter. Die Botschaft muss kurz und knapp sein da die Leute ja vorbeifahren.

```html
<!DOCTYPE html>
<html lang="de">
<head>
<meta charset="utf-8">
<title>Pfandhaus Plakat – Gold gegen Geld</title>
<link rel="stylesheet" href="https://fonts.googleapis.com/css2?family=Montserrat:ital,wght@0,700;0,800;0,900;1,900&display=swap">
<style>
  :root {
    --stage: #000000;
    --tan: #c8a066;
    --brown: #7b4a0b;
    --white: #ffffff;
    --shadow: #5e3a0c;
    --badge-red: #f0361c;
    --ink: #1a0d05;
  }
  html, body {
    margin: 0;
    padding: 0;
    width: 1200px;
    height: 849px;
    overflow: hidden;
    background: var(--stage);
  }
  .poster {
    position: absolute;
    left: 320px;
    top: 34px;
    width: 560px;
    height: 780px;
    background: linear-gradient(to right, var(--tan) 0 48.5%, var(--brown) 48.5% 100%);
    font-family: "Montserrat", sans-serif;
    overflow: hidden;
  }
  .headline {
    position: absolute;
    left: 150px;
    top: 22px;
    margin: 0;
    color: var(--white);
    font-weight: 900;
    line-height: 0.98;
    text-shadow: 5px 5px 0 var(--shadow);
  }
  .headline span { display: block; }
  .headline .big { font-size: 76px; letter-spacing: 1px; }
  .headline .small { font-size: 56px; font-style: italic; margin: -4px 0 2px 4px; }
  .badge {
    position: absolute;
    left: 368px;
    top: 146px;
    width: 180px;
    height: 180px;
  }
  .badge svg { position: absolute; inset: 0; }
  .badge-text {
    position: absolute;
    inset: 0;
    display: flex;
    flex-direction: column;
    justify-content: center;
    align-items: center;
    text-align: center;
    transform: rotate(12deg);
    color: var(--ink);
    font-weight: 800;
    font-size: 11.5px;
    line-height: 1.2;
  }
  .badge-text .lead { margin-bottom: 4px; }
  .product-photo {
    position: absolute;
    left: 135px;
    top: 280px;
    width: 290px;
    height: 240px;
    border-radius: 50%;
    background: radial-gradient(ellipse at 50% 48%, transparent 0 38%, rgba(0,0,0,0) 39%),
                linear-gradient(to right, #b8862e 0 46%, #a8684a 46% 100%);
    -webkit-mask: radial-gradient(ellipse at 50% 48%, transparent 0 37%, #000 38%);
            mask: radial-gradient(ellipse at 50% 48%, transparent 0 37%, #000 38%);
  }
  .tagline {
    position: absolute;
    left: 0;
    width: 546px;
    top: 532px;
    margin: 0;
    text-align: center;
    color: var(--white);
    font-weight: 700;
    font-size: 15.5px;
    line-height: 1.55;
  }
  .brand {
    position: absolute;
    left: 302px;
    top: 640px;
    width: 218px;
    text-align: center;
    color: var(--white);
    font-weight: 700;
    font-size: 17px;
    line-height: 1.35;
  }
  .web {
    position: absolute;
    left: 302px;
    top: 738px;
    width: 218px;
    text-align: center;
    color: var(--white);
    font-weight: 800;
    font-size: 17px;
  }
</style>
</head>
<body>
  <main class="poster">
    <h1 class="headline">
      <span class="big">GOLD</span>
      <span class="small">gegen</span>
      <span class="big">GELD</span>
    </h1>

    <div class="badge">
      <svg viewBox="0 0 180 180" aria-hidden="true">
        <circle cx="90" cy="90" r="80" fill="var(--badge-red)"/>
        <circle cx="90" cy="90" r="82" fill="none" stroke="var(--badge-red)" stroke-width="9" stroke-dasharray="10.7 10.7"/>
      </svg>
      <div class="badge-text">
        <span class="lead">Wir beleihen</span>
        <span>Schmuck, Uhren,</span>
        <span>Gold- &amp; Silberwaren,</span>
        <span>Technische Geräte,</span>
        <span>PKWs, alle Arten</span>
        <span>von Zweirädern</span>
      </div>
    </div>

    <div class="product-photo" role="img" aria-label="Foto: halb goldener Schmuckring, halb gerollte Geldscheine"></div>

    <p class="tagline">Machen Sie schnell Dinge zu Geld,<br>die schon lange rumliegen.</p>

    <div class="brand">Helmut Brandt<br>Pfandkredit</div>
    <div class="web">pfandkredit-brandt.de</div>
  </main>
</body>
</html>
```